Finding the Root: Reason in Clinical Choice-Crafting

I'd like a cover that looks like it would fit on the shelf next to "The Illness Mirage" by Corwin Talley, "The Close of Forgetting" by Hugh Marchetti, "Meal Mend" by Paul Grieve, "The Energy Restart Plan" by Oscar Pemberley or "The Gland Restart Plan" by the same or "The Cortex Restart Plan" by the same ... either text only (with some interesting fonts that make the title stand out, and the subtitle smaller) or a relevant image, though I'm not entirely sure what that would be since this is a book about big-picture medical decision making.
Author name is Dr Tessa Morrow, NMD
I'll eventually request an e-book, paperback, and audio cover from the winner...

Target Market(s)

practicing physicians

Industry/Entity Type

medicine

Requirements
Must have
• look similar to other books in the genre

```html
<!DOCTYPE html>
<html lang="en">
<head>
<meta charset="utf-8">
<title>Finding the Root: Reason in Clinical Choice-Crafting</title>
<link href="https://fonts.googleapis.com/css2?family=Oswald:wght@400;500;700&family=Bitter:wght@400&display=swap" rel="stylesheet">
<style>
  :root {
    --paper: #f2f1ea;
    --teal: #077f8e;
    --navy: #0b4f78;
    --ink: #111111;
    --rule: #222222;
    --art-tone: #e6e4da;
  }
  html, body {
    margin: 0;
    padding: 0;
    overflow: hidden;
    background: var(--paper);
  }
  .cover {
    position: relative;
    width: 927px;
    height: 1200px;
    background: var(--paper);
    overflow: hidden;
  }
  .cover__title {
    position: absolute;
    left: 0;
    top: 0;
    width: 927px;
    height: 640px;
  }
  .title-lead {
    font-family: 'Oswald', 'Arial Narrow', sans-serif;
    font-weight: 500;
    fill: var(--teal);
  }
  .title-key {
    font-family: 'Oswald', 'Arial Narrow', sans-serif;
    font-weight: 700;
    fill: var(--navy);
  }
  .title-art {
    fill: var(--art-tone);
  }
  .cover__subtitle {
    position: absolute;
    left: 0;
    top: 668px;
    width: 927px;
    margin: 0;
    text-align: center;
    font-family: 'Bitter', Georgia, serif;
    font-weight: 400;
    font-size: 66px;
    line-height: 80px;
    color: var(--ink);
    letter-spacing: 1px;
  }
  .cover__mark {
    position: absolute;
    left: 420px;
    top: 858px;
    width: 86px;
    height: 122px;
    background: var(--art-tone);
    border-radius: 40px 40px 20px 20px;
  }
  .cover__baseline {
    position: absolute;
    left: 0;
    top: 981px;
    width: 927px;
    height: 1px;
    background: var(--rule);
  }
  .cover__divider {
    position: absolute;
    left: 402px;
    top: 1033px;
    width: 122px;
    height: 3px;
    background: var(--navy);
  }
  .cover__author {
    position: absolute;
    left: 0;
    top: 1064px;
    width: 927px;
    margin: 0;
    text-align: center;
    font-family: 'Oswald', 'Arial Narrow', sans-serif;
    font-weight: 500;
    font-size: 54px;
    line-height: 60px;
    color: var(--ink);
    white-space: nowrap;
  }
  .credential {
    color: var(--teal);
    font-weight: 400;
    border-top: 2px solid var(--teal);
    border-bottom: 2px solid var(--teal);
    padding: 0 1px;
  }
</style>
</head>
<body>
  <main class="cover">
    <svg class="cover__title" viewBox="0 0 927 640" aria-label="Finding the Root">
      <text class="title-lead" x="99" y="247" font-size="172" textLength="730" lengthAdjust="spacingAndGlyphs">FINDING THE</text>
      <text class="title-key" x="104" y="623" font-size="420" textLength="718" lengthAdjust="spacingAndGlyphs">ROOT</text>
      <rect class="title-art" x="666" y="313" width="94" height="70" rx="30" role="img" aria-label="Small line drawing of a brain"/>
    </svg>

    <h2 class="cover__subtitle">Reason in Clinical<br>Choice-Crafting</h2>

    <div class="cover__mark" role="img" aria-label="Single-line drawing of a question mark"></div>
    <div class="cover__baseline"></div>
    <div class="cover__divider"></div>

    <p class="cover__author"><span class="credential">Dr</span> Tessa Morrow, <span class="credential">NMD</span></p>
  </main>
</body>
</html>
```